Halvik - consultancy website

I need a new design for my webpage/presence [to be functioning with Wordpress - I have a programmer to set it up but not the design idea].
My company is Halvik - a consultancy firm focused on growth management for Swedish SME's primarily;. We call it Leadership toolkit for firms on the rise, kind of a doctor helping small become big. Contentwise, its a simple frontpage + 3-4 subpages with content re company/myself/focus etc. The new site should communicate a fresh, trustworthy take yet simple and functional on all devices [i.e. think UI compatible for mobile/tablet]. Current building parts/form elements are
a) existing logo and text elements
b) existing pictures
c) the yellowish color
colours and new ideas on pictures/positioning are welcome. I prefer a 'full width page' solution with centralised text elements but that's all up to you to suggest. Current site is a quickfix made by myself - now I'm moving it to a new platform so want to take the opportunity to make it
Nothing superspecial as it is a 2-man show; on the other hand I still want to have a modern & fresh reflection of my brand in digital environments. Help me out!
www.halvik-demo.se
Best
Lina Bergqvist

```html
<!DOCTYPE html>
<html lang="en">
<head>
<meta charset="utf-8">
<title>Halvik – Contact Us</title>
<link href="https://fonts.googleapis.com/css2?family=Arimo:wght@400;700&family=Merriweather:wght@400&family=Open+Sans:wght@400&display=swap" rel="stylesheet">
<style>
:root{
  --accent:#f2a33b;
  --ink:#222;
  --text:#555;
  --muted:#888;
  --line:#ececec;
  --bar:#2b2b2b;
  --soft:#f7f7f7;
  --band:#333333;
  --foot:#1f1f1f;
  --foot-bottom:#161616;
  --social-a:#3b5998;
  --social-b:#3aa9e0;
  --social-c:#dd4b39;
}
*{margin:0;padding:0;box-sizing:border-box}
html,body{width:782px;height:1200px;overflow:hidden;background:#fff}
body{position:relative;font-family:Arimo,Arial,sans-serif;color:var(--ink)}
.abs{position:absolute}

.header{left:0;top:0;width:782px;height:86px;background:#fff}
.brand{left:64px;top:16px;font-family:Merriweather,Georgia,serif;font-size:30px;color:var(--ink);line-height:1}
.tagline{left:66px;top:52px;font-family:Merriweather,Georgia,serif;font-size:9.5px;color:var(--ink)}
.nav a{position:absolute;top:39px;font-size:9.5px;color:var(--ink);text-decoration:none}
.nav a.active{color:var(--accent)}
.nav .underline{position:absolute;left:669px;top:57px;width:69px;height:1px;background:var(--accent)}

.crumbs{left:0;top:86px;width:782px;height:35px;background:var(--bar);font-size:9px;color:#fff;padding:13px 0 0 64px}
.crumbs b{color:var(--accent)}

.page-title{left:0;top:164px;width:782px;text-align:center;font-size:16.5px;font-weight:700}
.intro{left:60px;top:199px;width:662px;text-align:center;font-size:8.8px;line-height:13.5px;color:var(--text)}

.col-title{top:279px;font-size:13.5px;letter-spacing:.4px;color:#333}
.field{left:53px;width:318px;border:1px solid var(--line);font-family:"Open Sans",Arial,sans-serif;font-size:7.3px;color:var(--muted);padding:11px 0 0 13px}
.field svg{position:absolute;right:11px;top:11px}
.send{left:53px;top:506px;width:318px;height:29px;background:var(--accent);color:#333;font-size:10px;letter-spacing:.6px;text-align:center;line-height:29px}
.office-photo{left:389px;top:314px;width:317px;height:221px;border:2px solid #e6e6e6;background:linear-gradient(180deg,#5d79a8 0%,#8fa0b8 30%,#6b5a48 55%,#1d2632 75%,#0c1118 100%)}

.info{left:0;top:587px;width:782px;height:249px;background:var(--soft)}
.card{top:630px;width:207px;height:165px;background:#fff;border:1px solid var(--line);text-align:center}
.card.featured{border-color:var(--accent)}
.card svg{position:absolute;left:50%;transform:translateX(-50%);top:29px}
.card h3{position:absolute;top:75px;width:100%;font-size:8.8px;font-weight:400;color:#333}
.card p{position:absolute;top:101px;width:100%;font-size:7.3px;line-height:13.5px;color:var(--muted)}

.cta{left:0;top:836px;width:782px;height:182px;background:var(--band);text-align:center;color:#fff}
.cta h2{position:absolute;top:50px;width:100%;font-size:20px;letter-spacing:3px;font-weight:700}
.cta h4{position:absolute;top:81px;width:100%;font-size:8.5px;letter-spacing:1.4px;font-weight:700}
.cta .btn{position:absolute;left:339px;top:107px;width:105px;height:27px;border:1.5px solid #fff;border-radius:3px;font-size:8.8px;font-weight:700;line-height:24px}

.footer{left:0;top:1018px;width:782px;height:149px;background:var(--foot);color:#fff}
.footer h5{position:absolute;top:30px;font-size:9px;font-weight:400}
.divider{position:absolute;top:26px;width:1px;height:103px;background:#3a3a3a}
.social{position:absolute;top:56px;width:47px;height:61px;text-align:center;font-size:8px}
.social i{display:block;margin:10px auto 0;width:25px;height:25px;border-radius:50%;background:rgba(255,255,255,.2)}
.social span{display:block;margin-top:11px}
.f-text{position:absolute;left:349px;top:52px;width:160px;font-size:7.3px;line-height:12.5px;color:#aaa}
.f-input{position:absolute;left:349px;top:85px;width:131px;height:18px;background:#fff;font-size:6.5px;color:#aaa;padding:5px 0 0 10px}
.f-ok{position:absolute;left:480px;top:85px;width:19px;height:18px;background:var(--accent)}
.f-note{position:absolute;left:349px;top:109px;font-size:6.5px;color:#888}
.menu{position:absolute;left:633px;top:58px;list-style:none;font-size:7.3px;line-height:14px}
.bottom{left:0;top:1167px;width:782px;height:33px;background:var(--foot-bottom);text-align:center;font-size:7px;color:#777;line-height:33px}
</style>
</head>
<body>

<header class="abs header">
  <div class="abs brand">Halvik.</div>
  <div class="abs tagline">Leadership toolkit for firms on the rise</div>
  <nav class="nav">
    <a style="left:400px">Home</a>
    <a style="left:467px">About Us</a>
    <a style="left:540px">Services</a>
    <a style="left:618px">Gallery</a>
    <a class="active" style="left:681px">Contact Us</a>
    <span class="underline"></span>
  </nav>
</header>

<div class="abs crumbs">Home &nbsp;&gt;&gt;&nbsp; <b>Contact Us</b></div>

<h1 class="abs page-title">Contact Us</h1>
<p class="abs intro">Donec eu viverra odio, eu cursus orci. Vestibulum id imperdiet est, non dictum leo. Aenean dictum nunc ex, quis vehicula dolor posuere id. Donec luctus luctus nisl, id porta turpis. Class aptent taciti sociosqu ad litora torquent per conubia nostra.</p>

<h2 class="abs col-title" style="left:53px;font-weight:400">Drop Us A Line</h2>
<h2 class="abs col-title" style="left:387px;font-weight:400">Our Office</h2>

<div class="abs field" style="top:314px;height:29px">First name
  <svg width="7" height="8" viewBox="0 0 7 8"><circle cx="3.5" cy="2" r="2" fill="#ccc"/><path d="M0 8a3.5 3 0 0 1 7 0z" fill="#ccc"/></svg></div>
<div class="abs field" style="top:349px;height:29px">Email address
  <svg width="8" height="6" viewBox="0 0 8 6"><rect x=".5" y=".5" width="7" height="5" fill="none" stroke="#ccc"/><path d="M.5.5 4 3.5 7.5.5" fill="none" stroke="#ccc"/></svg></div>
<div class="abs field" style="top:384px;height:29px">Phone Number
  <svg width="7" height="7" viewBox="0 0 7 7"><path d="M1 0 2.5 1.8 1.8 2.8a5 5 0 0 0 2.4 2.4L5.2 4.5 7 6 6 7A6 6 0 0 1 0 1z" fill="#ccc"/></svg></div>
<div class="abs field" style="top:419px;height:81px">Write message
  <svg width="8" height="6" viewBox="0 0 8 6"><ellipse cx="3.5" cy="2.5" rx="3.5" ry="2.5" fill="#ccc"/><ellipse cx="5" cy="3.5" rx="3" ry="2.2" fill="#ddd"/></svg></div>
<div class="abs send">SEND MESSAGE</div>

<div class="abs office-photo" role="img" aria-label="Photo of the office: waterfront apartment buildings at dusk with boats moored in the harbour"></div>

<section class="abs info">
</section>
<div class="abs card" style="left:53px">
  <svg width="14" height="19" viewBox="0 0 14 19"><path d="M7 0a7 7 0 0 1 7 7c0 5-7 12-7 12S0 12 0 7a7 7 0 0 1 7-7z" fill="var(--accent)"/><circle cx="7" cy="7" r="2.6" fill="#fff"/></svg>
  <h3>Address</h3>
  <p>Kajvägen 14B<br>120 64 Stockholm<br>Sweden</p>
</div>
<div class="abs card featured" style="left:276px">
  <svg width="18" height="18" viewBox="0 0 18 18"><path d="M3 0 7 4.5 5.2 7a12 12 0 0 0 5.8 5.8L13.5 11 18 15l-2.6 2.8C8 18 0 10 .2 2.6z" fill="var(--accent)"/></svg>
  <h3>Phone</h3>
  <p>+46 [0] 700 12 34 56</p>
</div>
<div class="abs card" style="left:499px">
  <svg width="23" height="17" viewBox="0 0 23 17"><rect width="23" height="17" rx="1.5" fill="var(--accent)"/><path d="M1 2l10.5 7.5L22 2" fill="none" stroke="#fff" stroke-width="1.6"/></svg>
  <h3>Email Address</h3>
  <p style="top:104px">info@halvik-demo.se</p>
</div>

<section class="abs cta">
  <h2>DONEC EU VIVERRA ODIO, EU CURSUS ORCI.</h2>
  <h4>IN VARIUS VENENATIS ELIT, A PLACERAT LACUS. MAURIS SUSCIPIT</h4>
  <div class="btn">CONTACT NOW</div>
</section>

<footer class="abs footer">
  <h5 style="left:64px">Let's Connect</h5>
  <div class="social" style="left:64px;background:var(--social-a)"><i></i><span>2598</span></div>
  <div class="social" style="left:116px;background:var(--social-b)"><i></i><span>4576</span></div>
  <div class="social" style="left:168px;background:var(--social-c)"><i></i><span>1269</span></div>
  <span class="divider" style="left:285px"></span>
  <h5 style="left:348px">Mailing List</h5>
  <p class="f-text">Sign up for our mailing list to get latest updates and offers.</p>
  <div class="f-input">Email address</div>
  <div class="f-ok"><svg width="19" height="18" viewBox="0 0 19 18"><path d="M6.5 9l2 2 4-4" fill="none" stroke="#fff" stroke-width="1.6"/></svg></div>
  <p class="f-note">We respect your privacy</p>
  <span class="divider" style="left:570px"></span>
  <h5 style="left:633px">Menu</h5>
  <ul class="menu"><li>Home</li><li>About Us</li><li>Services</li><li>Gallery</li><li>Contact Us</li></ul>
</footer>
<div class="abs bottom">© Copyrights 2015 All Rights Reserved</div>

</body>
</html>
```